Business Card Design Project

Looking to update our business cards. We have a logo with our slogan. We are an IT firm so we wouldlike a modern look.

Industry/Entity Type

Business

```html
<!DOCTYPE html>
<html lang="en">
<head>
<meta charset="utf-8">
<title>Upshift Business Card</title>
<link rel="stylesheet" href="https://fonts.googleapis.com/css2?family=Jost:wght@500&family=Libre+Baskerville:wght@400;700&display=swap">
<style>
  :root {
    --page: #ecebe7;
    --paper: #ffffff;
    --olive: #6b7f3e;
    --olive-light: #a9bb55;
    --ink-light: #ffffff;
    --brand-font: "Jost", sans-serif;
    --body-font: "Libre Baskerville", serif;
  }
  * { box-sizing: border-box; margin: 0; padding: 0; }
  html, body { width: 1200px; height: 699px; overflow: hidden; }
  body { background: var(--page); position: relative; }

  .card {
    position: absolute;
    width: 520px;
    height: 310px;
    border-radius: 20px;
    overflow: hidden;
    box-shadow: 0 6px 18px rgba(0,0,0,.18);
  }
  .card--front { left: 50px; top: 195px; background: var(--paper); }
  .card--back  { left: 630px; top: 195px; background: var(--olive); }

  /* front */
  .brand-lockup {
    position: absolute; left: 0; right: 0; top: 46px;
    display: flex; align-items: center; justify-content: center; gap: 14px;
  }
  .brand-mark-dot {
    width: 22px; height: 22px; border-radius: 50%; background: var(--olive-light);
  }
  .brand-name {
    font-family: var(--brand-font); font-weight: 500;
    font-size: 46px; letter-spacing: 10px; color: var(--olive); line-height: 1;
  }
  .band-rule {
    position: absolute; left: 0; right: 0; height: 2px; background: var(--olive-light);
  }
  .band-rule--top { top: 146px; }
  .band-rule--bottom { top: 256px; }
  .contact-band {
    position: absolute; left: 0; right: 0; top: 152px; height: 100px;
    background: var(--olive);
    display: flex; align-items: center; justify-content: center;
    color: var(--ink-light); font-family: var(--body-font); font-size: 14px;
  }
  .address { text-align: right; line-height: 1.6; padding-right: 16px; border-right: 1.5px solid var(--ink-light); }
  .contact-list { list-style: none; padding-left: 16px; line-height: 1.45; }
  .contact-list li { display: flex; align-items: center; gap: 8px; }
  .contact-list svg { width: 11px; height: 11px; flex: none; }
  .person-line {
    position: absolute; left: 0; right: 0; top: 268px; text-align: center;
    font-family: var(--body-font); color: var(--olive); font-size: 21px; font-weight: 700;
  }
  .person-line .person-title { font-weight: 400; font-size: 15px; color: var(--olive-light); }

  /* back */
  .back-lockup {
    position: absolute; left: 0; right: 0; top: 112px;
    display: flex; align-items: center; justify-content: center; gap: 16px;
  }
  .back-lockup .brand-mark-dot { background: var(--ink-light); width: 26px; height: 26px; }
  .back-lockup .brand-name { color: var(--ink-light); font-size: 56px; }
  .back-web {
    position: absolute; left: 0; right: 0; bottom: 46px; text-align: center;
    font-family: var(--brand-font); font-weight: 500; font-size: 22px;
    letter-spacing: 5px; color: var(--ink-light);
  }
</style>
</head>
<body>
  <section class="card card--front" aria-label="Business card front">
    <div class="brand-lockup">
      <span class="brand-mark-dot"></span>
      <span class="brand-name">UPSHIFT</span>
    </div>
    <div class="band-rule band-rule--top"></div>
    <div class="contact-band">
      <p class="address">12, Harbor Court<br>Lakeview, State 0817</p>
      <ul class="contact-list">
        <li><svg viewBox="0 0 12 12"><path fill="#ffffff" d="M2 1h2l1 3-1.5 1a7 7 0 0 0 3.5 3.5L8 7l3 1v2a1 1 0 0 1-1 1A9 9 0 0 1 1 2a1 1 0 0 1 1-1z"/></svg>0123 456789</li>
        <li><svg viewBox="0 0 12 12"><rect fill="#ffffff" x="3" y="0.5" width="6" height="11" rx="1"/></svg>0123 456789</li>
        <li><svg viewBox="0 0 12 12"><rect fill="#ffffff" x="0.5" y="2" width="11" height="8" rx="1"/><path d="M1 2.5l5 4 5-4" fill="none" stroke="#6b7f3e" stroke-width="1.2"/></svg>info@upshiftit.com</li>
        <li><svg viewBox="0 0 12 12"><circle fill="#ffffff" cx="6" cy="6" r="5.5"/></svg>www.upshiftit.com</li>
      </ul>
    </div>
    <div class="band-rule band-rule--bottom"></div>
    <p class="person-line">Your Name, <span class="person-title">Title</span></p>
  </section>

  <section class="card card--back" aria-label="Business card back">
    <div class="back-lockup">
      <span class="brand-mark-dot"></span>
      <span class="brand-name">UPSHIFT</span>
    </div>
    <p class="back-web">www.upshiftit.com</p>
  </section>
</body>
</html>
```